Business Card for Polygraph business in Africa

Business Card . Polygraph Examiner based in Tanzania, East Africa.
Business Card will be used to disseminate contact information to potential clients.
It should convey that I am a professional specifically in the polygraph field and perform my work with integrity.

I have attached the business card that I'm currently using, which I threw together myself initially. It's not professional enough.

Target Market(s)

Banks, Accounting Firms, Government Ministries, Gas, Oil, & Gemstone Mining Concerns, Wildlife Conservation NGOs, International companies located in East Africa.

Industry/Entity Type

Business

Contact Information for Business Card

Veritrace Kilonga
Miriam Holloway
PO Box 48317
Arusha, Tanzania
+255 612 839 274
miriamholloway@postvale.example

Colors
00a990
f37122
faa54b

Requirements
Must have
• - Veritrace Kilonga (with the word "Polygraph" being more prominent than the word "Tanzania")
• - Forensic Examinations
• - Employment Screening
• - Should contain a logo of the Continental Truthline Society (of which I'm a member)
• - I would like an accent design (such as the polygraph "squiggles" of a cardio tracing or such as that)
• - My contact information (less prominent, but large enough to read legibly). I would also consider putting the contact information on the second side of the card.
Nice to have
• My color suggestions are changeable.
Should not have
• Anything "cutesy" or "cartoonish"

```html
<!DOCTYPE html>
<html lang="en">
<head>
<meta charset="utf-8">
<title>Veritrace Kilonga – Business Card</title>
<link rel="stylesheet" href="https://fonts.googleapis.com/css2?family=Poppins:wght@300;400;600;700&display=swap">
<style>
  :root {
    --page-bg: #ececec;
    --brand-blue: #0b4fa6;
    --band-grey: #7d7d7d;
    --card-white: #ffffff;
    --text-light: #ffffff;
    --text-soft: #c9d8ee;
    --text-muted: #6f6f6f;
  }
  * { box-sizing: border-box; margin: 0; padding: 0; }
  html, body { width: 1200px; height: 886px; overflow: hidden; }
  body {
    background: var(--page-bg);
    font-family: "Poppins", sans-serif;
    position: relative;
  }
  .card {
    position: absolute;
    border-radius: 22px;
    overflow: hidden;
    box-shadow: 0 6px 18px rgba(0,0,0,0.15);
  }
  /* Front */
  .card-front {
    left: 125px; top: 163px;
    width: 330px; height: 560px;
    background: var(--brand-blue);
    color: var(--text-light);
    text-align: center;
  }
  .member-seal {
    display: block;
    margin: 44px auto 0;
    width: 70px; height: 70px;
  }
  .holder-name {
    margin-top: 14px;
    font-weight: 700;
    font-size: 21px;
    letter-spacing: 0.5px;
    text-transform: uppercase;
  }
  .holder-company {
    font-weight: 300;
    font-size: 15px;
    color: var(--text-soft);
    letter-spacing: 0.5px;
  }
  .divider {
    width: 40px; height: 1px;
    background: var(--text-light);
    margin: 12px auto 12px;
  }
  .contact-line {
    font-size: 11.5px;
    font-weight: 400;
    line-height: 1.6;
  }
  .tracing-band {
    position: absolute;
    left: 0; bottom: 0;
    width: 330px; height: 200px;
  }
  /* Back */
  .card-back {
    left: 515px; top: 278px;
    width: 560px; height: 330px;
    background: var(--card-white);
  }
  .brand-lockup {
    position: absolute;
    left: 0; right: 0; top: 120px;
    display: flex; align-items: center; justify-content: center;
    gap: 16px;
  }
  .brand-dot {
    width: 54px; height: 54px;
    border-radius: 50%;
    border: 4px solid var(--band-grey);
  }
  .brand-name {
    font-weight: 700;
    font-size: 38px;
    color: var(--brand-blue);
    letter-spacing: 0.5px;
  }
  .services {
    position: absolute;
    left: 0; right: 0; bottom: 34px;
    text-align: center;
    font-size: 12px;
    color: var(--text-muted);
    letter-spacing: 0.5px;
  }
</style>
</head>
<body>
  <section class="card card-front" aria-label="Card front">
    <svg class="member-seal" viewBox="0 0 70 70" role="img" aria-label="Continental Truthline Society membership badge">
      <circle cx="35" cy="35" r="34" fill="#ffffff"/>
      <circle cx="35" cy="35" r="27" fill="none" stroke="#2b3f9e" stroke-width="2"/>
    </svg>
    <h1 class="holder-name">Miriam Holloway</h1>
    <p class="holder-company">Veritrace Kilonga</p>
    <div class="divider"></div>
    <p class="contact-line">PO Box 48317, Arusha, Tanzania</p>
    <p class="contact-line">+255 612 839 274 | miriamholloway@postvale.example</p>
    <p class="contact-line">www.miriamholloway.example</p>
    <svg class="tracing-band" viewBox="0 0 330 200" role="img" aria-label="Polygraph tracing accent over grey band">
      <rect x="0" y="60" width="330" height="140" fill="var(--band-grey)"/>
      <rect x="0" y="56" width="330" height="6" fill="#ffffff"/>
    </svg>
  </section>

  <section class="card card-back" aria-label="Card back">
    <div class="brand-lockup">
      <span class="brand-dot"></span>
      <span class="brand-name">Veritrace Kilonga</span>
    </div>
    <p class="services">Forensic Examinations | Employment Screening</p>
  </section>
</body>
</html>
```